Logo, Web and Mobile Designs for enterprise social media platform

All the details are in the attached document, please start reading the scope document first which explains what is this project about and the details about the needed deliverables, after that please read the UI_Requirements document which will detail what is expected regarding the coded web version since this is a coded contest, it is very important that you meet the UI requirements or suggest something else but we will need to agree first before working on the coded version

Good Luck

Target Market(s)

Enterprise Social Media

Industry/Entity Type

Media

Coding

Coded - Design and coding required

Number of Pages Required

5+ page

Font styles to use
Sans Serif

Requirements
Must have
• All the must haves are listed in the scope document so please check before you start

```html
<!DOCTYPE html>
<html lang="en">
<head>
<meta charset="utf-8">
<title>Workvista – Professional Network</title>
<link rel="stylesheet" href="https://fonts.googleapis.com/css2?family=Open+Sans:wght@300;400;600&family=Roboto:wght@400;500&display=swap">
<style>
  :root {
    --hero-top: #34401a;
    --hero-mid: #1c230c;
    --hero-bottom: #070805;
    --white: #ffffff;
    --accent: #0099d6;
    --divider: rgba(255,255,255,0.18);
    --footer-bg: #f3f3f3;
    --footer-text: #5a5a5a;
    --placeholder: #9a9a9a;
    --ink: #222222;
  }
  * { box-sizing: border-box; margin: 0; padding: 0; }
  html, body { width: 1200px; height: 850px; overflow: hidden; }
  body { font-family: "Open Sans", sans-serif; color: var(--white); position: relative; background: var(--hero-bottom); }

  .hero { position: absolute; left: 0; top: 0; width: 1200px; height: 750px; }
  .hero-backdrop {
    position: absolute; inset: 0;
    background:
      radial-gradient(ellipse at 60% 30%, rgba(70,85,30,0.55), transparent 60%),
      linear-gradient(180deg, var(--hero-top) 0%, var(--hero-mid) 55%, var(--hero-bottom) 100%);
  }

  .brand { position: absolute; left: 99px; top: 45px; font-size: 27px; font-weight: 400; letter-spacing: 0.2px; }
  .menu-toggle { position: absolute; left: 1074px; top: 51px; }

  .headline { position: absolute; left: 0; width: 1200px; top: 230px; text-align: center; font-family: "Roboto", sans-serif; font-weight: 500; font-size: 36px; letter-spacing: 0.3px; }
  .tagline { position: absolute; left: 0; width: 1200px; top: 288px; text-align: center; font-weight: 300; font-size: 54px; line-height: 63px; }

  .btn { position: absolute; top: 449px; width: 165px; height: 48px; display: flex; align-items: center; justify-content: center; font-size: 22px; border-radius: 2px; }
  .btn-join { left: 427px; background: var(--white); color: var(--ink); }
  .btn-signin { left: 609px; background: var(--accent); color: var(--white); }

  .divider { position: absolute; left: 99px; top: 594px; width: 1002px; height: 1px; background: var(--divider); }

  .finder-label { position: absolute; left: 98px; top: 634px; font-size: 21px; }
  .field { position: absolute; top: 627px; width: 248px; height: 47px; background: var(--white); border-radius: 2px; color: var(--placeholder); font-family: "Roboto", sans-serif; font-size: 14px; padding-left: 15px; display: flex; align-items: center; }
  .field-first { left: 296px; }
  .field-last { left: 562px; }
  .btn-search { position: absolute; left: 831px; top: 627px; width: 131px; height: 47px; background: var(--accent); border-radius: 12px; display: flex; align-items: center; justify-content: center; font-family: "Roboto", sans-serif; font-size: 19px; }

  .legal-note { position: absolute; left: 0; width: 1200px; top: 701px; text-align: center; font-size: 13px; }
  .legal-note a { color: var(--white); text-decoration: underline; }

  .site-footer { position: absolute; left: 0; top: 750px; width: 1200px; height: 100px; background: var(--footer-bg); color: var(--footer-text); font-size: 13.5px; padding: 26px 99px 0; line-height: 28px; }
  .site-footer span { white-space: nowrap; }
</style>
</head>
<body>
  <section class="hero">
    <div class="hero-backdrop" role="img" aria-label="Dimmed photo of colleagues talking in a bright office"></div>
    <div class="brand">Workvista</div>
    <svg class="menu-toggle" width="28" height="24" viewBox="0 0 28 24" aria-label="Menu">
      <rect x="0" y="0" width="28" height="5" fill="#fff"/>
      <rect x="0" y="9.5" width="28" height="5" fill="#fff"/>
      <rect x="0" y="19" width="28" height="5" fill="#fff"/>
    </svg>
    <h1 class="headline">Join the world’s largest professional network</h1>
    <p class="tagline">Opportunity is always<br>within reach</p>
    <div class="btn btn-join">Join</div>
    <div class="btn btn-signin">Sign in</div>

    <div class="divider"></div>
    <div class="finder-label">Find a Colleague :</div>
    <div class="field field-first">First Name</div>
    <div class="field field-last">Last Name</div>
    <div class="btn-search">Search</div>
    <p class="legal-note">All application can be found in your settings <a>Terms of Services | Privacy Polocy</a></p>
  </section>

  <footer class="site-footer">
    <span>Help Center | About | Press | Blog | Careers | Mobile | Developers | Workvista Updates | Workvista Influencers | Workvista Jobs | Job Directory | Company Directory |</span><br>
    <span>Groups Diectory | User Agreement | Privacy Policy | Cookie Policy | Copyright Policy.</span>
  </footer>
</body>
</html>
```